Business card design needed

Front of Card:
I would like to have nearly 3/4 of the card from the top in a Pea Green Colour with the word 'Brambleway' written in a(Watermelon Red colour) in the font 'Viner Hand ITC'. Brambleway to be written within the Green colour of the card.

The lower 1/3 of the card I would like to have white with the words:
Home and Garden Styling smaller than the word Brambleway in Black in the font 'Batang', centred underneath the green section.

At the very bottom in one corner in smaller print I would like to have my contact phone number: Pia M:0437619204 and then the email address:
E: brambleaystudio@kelnor.net.au on the other side.

Back of Card:
Back of Card to be White
On one side (Left)
I would like the Heading "Garden" in the same pea green colour as the front and in the Viner Hand ITC font. On the other half of the card I would like 'Home' in the Watermelon Red Colour (same as front colour) and in the font Viner Hand ITC.
Underneath these Headings I would like written in black and in Batang font the following list of services.

Garden Home
Garden Styling Interior Styling
Plant Selection Furniture Selection/Arrangement Garden Maintenance Setting Up Home (after move)
Hedging/Mowing Merchandise and Stylist for
Work w/Local Nurseries Marrow and Finch

Brambleway
Home and Garden Styling
M: 0437619204 E: brambleaystudio@kelnor.net.au

```html
<!DOCTYPE html>
<html lang="en">
<head>
<meta charset="utf-8">
<title>Brambleway – Business Card</title>
<link rel="stylesheet" href="https://fonts.googleapis.com/css2?family=Caveat+Brush&family=Nanum+Myeongjo:wght@400;700&display=swap">
<style>
  :root {
    --pea-green: #217a35;
    --watermelon: #e84a6e;
    --ink: #2b2b2b;
    --paper: #ffffff;
    --backdrop: #eeefef;
    --edge: #d4d4d4;
    --script: "Caveat Brush", cursive;
    --serif: "Nanum Myeongjo", serif;
  }
  * { margin: 0; padding: 0; box-sizing: border-box; }
  html, body { width: 1063px; height: 1200px; overflow: hidden; }
  body { background: var(--backdrop); position: relative; font-family: var(--serif); color: var(--ink); }

  .card {
    position: absolute;
    width: 876px;
    height: 486px;
    background: var(--paper);
    border: 1px solid var(--edge);
    box-shadow: 0 10px 24px rgba(0,0,0,0.08);
    overflow: hidden;
  }
  .card--front { left: 79px; top: 89px; }
  .card--back  { left: 75px; top: 609px; width: 875px; height: 485px; }

  /* Front */
  .front__band {
    position: absolute; left: 0; top: 0; width: 100%; height: 314px;
    background: var(--pea-green);
  }
  .front__name { position: absolute; left: 78px; top: 70px; width: 720px; height: 190px; }
  .front__name text { font-family: var(--script); fill: var(--watermelon); font-size: 170px; }
  .front__tagline {
    position: absolute; left: 0; top: 322px; width: 100%;
    text-align: center; font-size: 54px; font-weight: 400; letter-spacing: 0.5px;
  }
  .front__contact {
    position: absolute; top: 421px; display: flex; align-items: center; gap: 6px;
    font-size: 25px; font-weight: 700;
  }
  .front__contact--phone { left: 88px; }
  .front__contact--email { left: 336px; gap: 10px; }
  .front__contact svg { flex: none; }

  /* Back */
  .services__heading {
    position: absolute; top: 62px; font-family: var(--script); font-size: 62px; font-weight: 400;
  }
  .services__heading--garden { left: 86px; color: var(--pea-green); }
  .services__heading--home { left: 452px; color: var(--watermelon); }
  .services__list {
    position: absolute; top: 188px; list-style: none;
    font-size: 23px; line-height: 38px; letter-spacing: 0.3px;
  }
  .services__list--garden { left: 80px; }
  .services__list--home { left: 442px; }
  .services__list li { position: relative; padding-left: 16px; }
  .services__list li::before {
    content: ""; position: absolute; left: 0; top: 16px; width: 7px; height: 7px; border-radius: 50%;
  }
  .services__list--garden li::before { background: var(--pea-green); }
  .services__list--home li::before { background: var(--watermelon); }
  .services__list li.no-bullet::before { display: none; }
  .back__stripe { position: absolute; left: 0; bottom: 0; width: 100%; height: 29px; }
</style>
</head>
<body>

<section class="card card--front">
  <div class="front__band"></div>
  <svg class="front__name" viewBox="0 0 720 190" aria-label="Brambleway">
    <text x="0" y="150" textLength="720" lengthAdjust="spacingAndGlyphs">Brambleway</text>
  </svg>
  <h2 class="front__tagline">Home and Garden Styling</h2>
  <div class="front__contact front__contact--phone">
    <svg width="20" height="24" viewBox="0 0 20 24" aria-hidden="true">
      <path d="M5 1 L9 6 L6.5 9 C7.5 12 9.5 15 12 17 L15 14.5 L19 19 L16 22.5 C9 22 2 13 2.5 4 Z" fill="var(--ink)"/>
    </svg>
    <span>0437619204</span>
  </div>
  <div class="front__contact front__contact--email">
    <svg width="26" height="18" viewBox="0 0 26 18" aria-hidden="true">
      <rect x="1" y="1" width="24" height="16" fill="none" stroke="var(--ink)" stroke-width="1.6"/>
      <path d="M1 1 L13 10 L25 1 M1 17 L10 8 M25 17 L16 8" fill="none" stroke="var(--ink)" stroke-width="1.4"/>
    </svg>
    <span>brambleaystudio@kelnor.net.au</span>
  </div>
</section>

<section class="card card--back">
  <h3 class="services__heading services__heading--garden">Garden</h3>
  <h3 class="services__heading services__heading--home">Home</h3>
  <ul class="services__list services__list--garden">
    <li>Garden Styling</li>
    <li>Plant Selection</li>
    <li>Garden Maintenance</li>
    <li>Hadging/Mowing</li>
    <li>Work w/Local Nurseries</li>
  </ul>
  <ul class="services__list services__list--home">
    <li>Interior Styling</li>
    <li>Furniture Selection/Arrangement</li>
    <li>Setting Up Home (after move)</li>
    <li>Merchandise and Stylist</li>
    <li class="no-bullet">for Marrow and Finch</li>
  </ul>
  <svg class="back__stripe" viewBox="0 0 875 29" preserveAspectRatio="none" aria-hidden="true">
    <rect x="0" y="0" width="875" height="29" fill="var(--watermelon)"/>
    <polygon points="0,0 468,0 419,29 0,29" fill="var(--pea-green)"/>
  </svg>
</section>

</body>
</html>
```